High-end construction company needs a business card design

We need a modern looking business card that draws people in, is memorable and looks so good people will want to sick it on their fridges.
On the first side what is needed are:
Logo
My name - Tomasz Brelwik
Title - Managing Director
Website - www.varkelt.co.uk
Email - tomasz@varkelt.co.uk
Telephone - 020 5194 6281
Mobile - 07845139072
On the back side was is needed is a list of all the services we provide:
-Kitchen Renovations
-Bathroom Renovations
-House Renovations
-Garage Conversions
-Extensions
-Loft Conversions
-Conservatories
-Carpentry
-Tiling
-Electrical
-Plumbing & Heating
-Bricklaying
-Landscaping
-Decorating
-Plastering
We would like the colours to be the same shades as on the logo with grey or black for the words.
Target Market(s)
Anyone who needs building work done
Contact Information for Business Card
This business card is for a construction company which strives to deliver excellent service and quality.
The look and feel of the card should represent this.
Requirements
Must have
- On the first side what is needed are:
Logo
My name - Tomasz Brelwik
Title - Managing Director
Website - www.varkelt.co.uk
Email - tomasz@varkelt.co.uk
Telephone - 020 5194 6281
Mobile - 07845139072
Nice to have
- Cool looking features

```html
<!DOCTYPE html>
<html lang="en">
<head>
<meta charset="utf-8">
<title>Varkelt Construction Ltd – Business Card</title>
<link href="https://fonts.googleapis.com/css2?family=Montserrat:wght@400;500;700&display=swap" rel="stylesheet">
<style>
  :root {
    --green-deep: #4a8f3f;
    --green-bright: #6cc04a;
    --ink: #3a3a3a;
    --paper: #ffffff;
    --backdrop: #e6e8e6;
  }
  * { box-sizing: border-box; margin: 0; padding: 0; }
  html, body { width: 1200px; height: 900px; overflow: hidden; }
  body {
    background: var(--backdrop);
    font-family: "Montserrat", Arial, sans-serif;
    position: relative;
  }
  .card {
    position: absolute;
    left: 250px;
    width: 700px;
    height: 400px;
    overflow: hidden;
    box-shadow: 0 6px 18px rgba(0,0,0,0.18);
  }
  /* Back side */
  .card-back {
    top: 30px;
    background: var(--green-deep);
    color: var(--paper);
    text-align: center;
  }
  .card-back .brand {
    margin-top: 92px;
  }
  .brand-name {
    font-weight: 700;
    font-size: 58px;
    letter-spacing: 4px;
    line-height: 1;
  }
  .brand-sub {
    font-weight: 700;
    font-size: 20px;
    letter-spacing: 6px;
    margin-top: 8px;
  }
  .card-back .brand-name,
  .card-back .brand-sub { color: var(--paper); }
  .services {
    list-style: none;
    margin-top: 34px;
    font-size: 16px;
    line-height: 1.45;
    font-weight: 400;
  }
  /* Front side */
  .card-front {
    top: 470px;
    background: var(--paper);
  }
  .swoosh {
    position: absolute;
    left: 0; top: 0;
    width: 700px; height: 400px;
  }
  .front-brand {
    position: absolute;
    left: 40px;
    top: 96px;
    width: 290px;
    text-align: center;
  }
  .front-brand .brand-name,
  .front-brand .brand-sub { color: var(--green-bright); }
  .front-brand .brand-name { font-size: 48px; }
  .front-brand .brand-sub { font-size: 16px; letter-spacing: 5px; }
  .divider {
    position: absolute;
    left: 355px;
    top: 50px;
    width: 2px;
    height: 215px;
    background: var(--green-bright);
  }
  .contact {
    position: absolute;
    left: 385px;
    top: 52px;
    color: var(--ink);
  }
  .contact-name {
    color: var(--green-bright);
    font-weight: 700;
    font-size: 26px;
  }
  .contact-title {
    font-size: 16px;
    font-weight: 500;
    margin-top: 2px;
  }
  .contact-address {
    font-style: normal;
    font-size: 16px;
    line-height: 1.35;
    margin-top: 14px;
  }
  .contact-lines {
    list-style: none;
    margin-top: 12px;
    font-size: 16px;
    line-height: 1.5;
  }
  .contact-lines li { display: flex; align-items: center; gap: 8px; }
  .icon { width: 13px; height: 13px; flex: none; }
</style>
</head>
<body>

<section class="card card-back" aria-label="Card back – services">
  <div class="brand">
    <div class="brand-name">VARKELT</div>
    <div class="brand-sub">CONSTRUCTION LTD</div>
  </div>
  <ul class="services">
    <li>Kitchen Renovations | Bathroom Renovations</li>
    <li>House Renovations | Garage Conversions | Extensions</li>
    <li>Loft Conversions | Conservatories | Carpentry | Tiling | Electrical</li>
    <li>Plumbing &amp; Heating | Bricklaying | Landscaping | Decorating | Plastering</li>
  </ul>
</section>

<section class="card card-front" aria-label="Card front – contact">
  <svg class="swoosh" viewBox="0 0 700 400" aria-hidden="true">
    <path d="M0 270 C 140 300, 300 360, 400 330 C 500 300, 560 330, 600 400 L 0 400 Z" fill="var(--green-deep)"/>
    <path d="M0 255 C 150 290, 300 350, 400 320 C 500 292, 565 320, 605 400" fill="none" stroke="var(--green-bright)" stroke-width="4"/>
    <path d="M0 262 C 150 296, 300 356, 400 326 C 500 297, 562 325, 602 400" fill="none" stroke="var(--paper)" stroke-width="4"/>
  </svg>

  <div class="front-brand">
    <div class="brand-name">VARKELT</div>
    <div class="brand-sub">CONSTRUCTION LTD</div>
  </div>

  <div class="divider"></div>

  <div class="contact">
    <div class="contact-name">Tomasz Brelwik</div>
    <div class="contact-title">Managing Director</div>
    <address class="contact-address">14-16 Halden Street,<br>London, N4 2QP</address>
    <ul class="contact-lines">
      <li>
        <svg class="icon" viewBox="0 0 16 16" aria-hidden="true"><path d="M4 1l3 3-2 2c1 2 3 4 5 5l2-2 3 3-2 3C7 15 1 9 1 3z" fill="var(--green-bright)"/></svg>
        020 5194 6281
      </li>
      <li>
        <svg class="icon" viewBox="0 0 16 16" aria-hidden="true"><rect x="4" y="1" width="8" height="14" rx="1.5" fill="none" stroke="var(--green-bright)" stroke-width="1.8"/></svg>
        07845139072
      </li>
      <li>
        <svg class="icon" viewBox="0 0 16 16" aria-hidden="true"><rect x="1" y="3" width="14" height="10" fill="none" stroke="var(--green-bright)" stroke-width="1.6"/><path d="M1 3l7 6 7-6" fill="none" stroke="var(--green-bright)" stroke-width="1.6"/></svg>
        tomasz@varkelt.co.uk
      </li>
      <li>
        <svg class="icon" viewBox="0 0 16 16" aria-hidden="true"><circle cx="8" cy="8" r="6.5" fill="none" stroke="var(--green-bright)" stroke-width="1.5"/><path d="M1.5 8h13M8 1.5c-3 3.5-3 9.5 0 13M8 1.5c3 3.5 3 9.5 0 13" fill="none" stroke="var(--green-bright)" stroke-width="1.2"/></svg>
        www.varkelt.co.uk
      </li>
    </ul>
  </div>
</section>

</body>
</html>
```